Letterhead and matching envelope design for a dental office

We need a new stationary design, letterhead and envelope #10, for a dental office in Denver area. We are called Bright Harbor Dental. We want a simple and minimalistic design but not a boring design. I wish to have one good point that makes it look professional. I have attached our logo. Feel free to use either one. I want the design for letterhead and envelope look like a "matching pair" but not look the same. The envelope doesn't have to be white and it will have an address window on bottom left.

Target Market(s)

everyone who visits dentist (adults)

Industry/Entity Type

Dental

Font styles to use
Other font styles liked:
• close to font on logo or something that matches well

Requirements
Must have
• professional
• simple, minimalistic
• unique point that stands out
Nice to have
• matching but not same design for letterhead and envelope
Should not have
• not look like all the other boring designs
• no flowery, distracting feats

```html
<!DOCTYPE html>
<html lang="en">
<head>
<meta charset="utf-8">
<title>Bright Harbor Dental – Envelope #10</title>
<link href="https://fonts.googleapis.com/css2?family=Source+Sans+3:wght@400;600&display=swap" rel="stylesheet">
<style>
  :root {
    --backdrop: #c9c9c9;
    --paper: #ffffff;
    --brand-green: #3bb54a;
    --pale-green: #b9dfbe;
    --mist-green: #e6f3e6;
    --ink: #222222;
    --rule-grey: #b5b5b5;
    --box-border: #c4c4c4;
  }
  * { box-sizing: border-box; margin: 0; padding: 0; }
  html, body {
    width: 1200px; height: 848px; overflow: hidden;
    background: var(--backdrop);
    font-family: "Source Sans 3", sans-serif;
  }
  .canvas { position: relative; width: 1200px; height: 848px; }

  .envelope-front {
    position: absolute; left: 220px; top: 82px; width: 760px; height: 330px;
    background: var(--paper); overflow: hidden;
  }
  .brand-mark {
    position: absolute; left: 36px; top: 44px;
    display: flex; align-items: center; gap: 14px;
  }
  .brand-dot {
    width: 22px; height: 22px; border-radius: 50%;
    background: var(--brand-green);
  }
  .brand-name {
    color: var(--brand-green); font-weight: 600; font-size: 24px;
    letter-spacing: 3px; text-transform: uppercase;
  }
  .decor-glow {
    position: absolute; left: 390px; top: 70px; width: 320px; height: 230px;
    background: radial-gradient(ellipse at center, var(--mist-green) 0%, rgba(230,243,230,0.6) 45%, rgba(255,255,255,0) 72%);
  }
  .address-window {
    position: absolute; left: 33px; top: 139px; width: 260px; height: 90px;
    border: 1.5px solid var(--box-border); border-radius: 9px;
    padding: 5px 10px 0 10px;
  }
  .address-label { font-size: 8px; font-weight: 600; color: var(--ink); line-height: 10px; }
  .address-line { border-bottom: 1px dotted var(--rule-grey); height: 14px; }
  .address-line:first-of-type { height: 5px; }
  .return-address {
    position: absolute; left: 33px; top: 260px;
    font-size: 13px; line-height: 17px; color: var(--ink);
  }
  .return-address .sender { color: var(--brand-green); }
  .front-band {
    position: absolute; left: 0; bottom: 0; width: 100%; height: 8px;
    background: var(--pale-green);
  }
  .web-tab { position: absolute; left: 472px; top: 304px; width: 218px; height: 26px; }
  .web-address {
    position: absolute; left: 472px; top: 304px; width: 218px; height: 26px;
    color: var(--paper); font-size: 13px; line-height: 28px; text-align: center;
  }

  .envelope-back {
    position: absolute; left: 220px; top: 428px; width: 760px; height: 332px;
    background: var(--paper);
  }
  .flap { position: absolute; left: 0; top: 0; width: 760px; height: 140px; }
  .flap-mark {
    position: absolute; left: 0; top: 46px; width: 760px;
    display: flex; justify-content: center; align-items: center; gap: 8px;
  }
  .flap-dot { width: 10px; height: 10px; border-radius: 50%; background: var(--paper); }
  .flap-name {
    color: var(--paper); font-weight: 600; font-size: 13px;
    letter-spacing: 3px; text-transform: uppercase;
  }
</style>
</head>
<body>
<div class="canvas">

  <section class="envelope-front">
    <div class="decor-glow" role="img" aria-label="Faint pale green brand decoration"></div>

    <div class="brand-mark">
      <span class="brand-dot"></span>
      <span class="brand-name">Bright Harbor Dental</span>
    </div>

    <div class="address-window">
      <p class="address-label">To</p>
      <div class="address-line"></div>
      <div class="address-line"></div>
      <div class="address-line"></div>
      <div class="address-line"></div>
      <div class="address-line"></div>
      <div class="address-line"></div>
    </div>

    <address class="return-address" style="font-style:normal">
      <span class="sender">Bright Harbor Dental</span><br>
      2480 Lakeview Blvd,<br>
      Suite 210 Arvada, CO 80003
    </address>

    <div class="front-band"></div>
    <svg class="web-tab" viewBox="0 0 218 26" aria-hidden="true">
      <polygon points="0,26 12,0 204,0 218,26" fill="#ffffff"/>
      <polygon points="5,26 15,3 201,3 212,26" fill="#3bb54a"/>
    </svg>
    <p class="web-address">www.brightharbordental.com</p>
  </section>

  <section class="envelope-back">
    <svg class="flap" viewBox="0 0 760 140" aria-hidden="true">
      <path d="M0,2 L760,2 C752,40 745,58 700,70 L420,128 C395,134 365,134 340,128 L60,70 C15,58 8,40 0,2 Z" fill="#3bb54a"/>
    </svg>
    <div class="flap-mark">
      <span class="flap-dot"></span>
      <span class="flap-name">Bright Harbor Dental</span>
    </div>
  </section>

</div>
</body>
</html>
```